Meridale Partners Website

Meridale Partners (MP) provide Analytics & Enterprise Performance Management (EPM) advisory & consultancy services. We are passionate about data and making a difference for our clients by working in partnership with them, helping them on their journey to becoming an Meridale Partner. We deliver insights which give our clients a competitive edge and a much deeper understanding of their organisation.

We need a website which shows who we are, what we do and how we do it.

www.meridale-partners.example is our very basic website at the moment. We want to completely revamp it with a corporate look

```html
<!DOCTYPE html>
<html lang="en">
<head>
<meta charset="utf-8">
<title>Meridale Partners – Data Analytics &amp; EPM Consulting</title>
<link href="https://fonts.googleapis.com/css2?family=Poppins:wght@400;500;600;700;800&display=swap" rel="stylesheet">
<style>
:root{
  --orange:#ff7a00;
  --navy:#1b2838;
  --ink:#1f2a3a;
  --band:#2f4563;
  --footer:#1d2a3d;
  --label:#1a6fd6;
  --white:#ffffff;
  --text:#333c48;
  --muted:#c9d0da;
  --badge:#4a5a70;
}
*{margin:0;padding:0;box-sizing:border-box}
html,body{width:1200px;height:2727px;overflow:hidden}
body{position:relative;font-family:'Poppins',sans-serif;color:var(--text);background:var(--white)}
.abs{position:absolute}
a{color:inherit;text-decoration:none}

.hero{left:0;top:0;width:1200px;height:747px;background:linear-gradient(120deg,#2a3038 0%,#3d4550 45%,#55575a 70%,#2b2f35 100%)}
.hero-shade{left:0;top:0;width:1200px;height:747px;background:linear-gradient(90deg,rgba(15,20,28,.75) 0%,rgba(15,20,28,.3) 60%,rgba(15,20,28,.1) 100%)}
.brand{display:flex;align-items:center;gap:12px;color:var(--white);font-weight:600;font-size:19px;line-height:22px;letter-spacing:.5px}
.brand-mark{width:58px;height:58px;border-radius:50%;border:7px solid var(--white)}
.nav{top:52px;left:562px;display:flex;gap:40px;font-size:13px;font-weight:600;color:var(--white);letter-spacing:.3px}
.nav .active{color:var(--orange)}
.hero-phone{top:43px;left:976px;display:flex;align-items:center;gap:12px;color:var(--white);font-weight:600;font-size:19px}
.ring{width:34px;height:34px;border-radius:50%;border:1.5px solid var(--white);display:flex;align-items:center;justify-content:center}
.hero-title{left:72px;top:238px;color:var(--white);font-size:82px;font-weight:800;line-height:82px}
.hero-sub{left:73px;top:418px;color:var(--white);font-size:36px;font-weight:700;line-height:43px}
.scroll{left:0;width:1200px;top:688px;text-align:center;color:var(--white);font-size:13px}
.scroll-line{left:599px;top:713px;width:2px;height:85px;background:#c9ccd1}

.label{font-size:13px;font-weight:500;color:var(--label);letter-spacing:.3px}
.h2{font-size:42px;font-weight:700;color:var(--ink);line-height:50px}
.btn{display:flex;align-items:center;justify-content:center;background:var(--orange);color:var(--white);font-weight:600;font-size:16px}

.about-lead{left:74px;top:926px;width:540px;font-size:17px;line-height:30.5px;font-weight:500;color:var(--orange);white-space:nowrap}
.about-body{left:74px;top:1064px;width:540px;font-size:15px;line-height:28px;color:var(--text);white-space:nowrap}
.photo{background:linear-gradient(135deg,#d7dde3,#9aa6b1)}
.photo.warm{background:linear-gradient(135deg,#2d3440,#a0623b)}

.services{left:0;top:1371px;width:1200px;height:505px;background:linear-gradient(135deg,#1f2f47 0%,#16253b 60%,#1d2d44 100%)}
.svc{width:329px;height:273px;border:1px solid rgba(255,255,255,.35);overflow:hidden;text-align:center;color:var(--white)}
.dome{position:absolute;left:58px;width:212px;height:212px;border-radius:50%;background:var(--orange)}
.svc h3{position:absolute;left:0;width:100%;font-size:22px;font-weight:700}
.svc p{position:absolute;left:24px;width:281px;font-size:14px;line-height:24px;color:#e4e8ee}

.process-body{left:74px;top:2030px;width:370px;font-size:15.5px;line-height:28px;color:var(--text);white-space:nowrap}
.panel{left:467px;top:1975px;width:640px;height:245px;background:var(--navy)}
.panel-inner{left:474px;top:1982px;width:626px;height:231px;border:1.5px solid #8b97a8}
.step{text-align:center;width:210px}
.step h4{font-size:23px;font-weight:700;margin-top:6px}
.step p{font-size:14px;line-height:23px;margin-top:6px}
.step.dark{color:var(--white)}
.step.dark p{color:#dfe4ea}
.step.light h4{color:var(--ink)}
.step.light p{color:#555e6a}
.step-card{left:678px;top:1962px;width:221px;height:270px;background:#f7f7f7;box-shadow:0 6px 20px rgba(0,0,0,.12)}

.cta{left:0;top:2336px;width:1200px;height:132px;background:var(--band)}
.cta-text{left:100px;top:2385px;color:var(--white);font-size:26px;font-weight:700;letter-spacing:.3px}

.footer{left:0;top:2468px;width:1200px;height:259px;background:var(--footer)}
.f-head{font-size:14px;font-weight:700;color:var(--white);letter-spacing:.3px}
.f-list{font-size:15px;color:var(--muted);line-height:36px}
.f-copy{left:74px;top:2606px;font-size:14px;line-height:25px;color:var(--muted)}
.f-contact{left:560px;font-size:15px;color:var(--muted);display:flex;gap:14px;line-height:23px}
.social{top:2651px;left:885px;display:flex;gap:26px}
.social i{width:24px;height:24px;border-radius:3px;background:var(--white);display:block}
.partner-badge{left:885px;top:2548px;width:204px;height:32px;border:2px solid var(--badge);background:transparent}
</style>
</head>
<body>

<div class="abs hero" role="img" aria-label="Photo of a team meeting around a table with a presenter and dashboard screen"></div>
<div class="abs hero-shade"></div>
<div class="abs brand" style="left:75px;top:30px"><div class="brand-mark"></div><div>MERIDALE<br>PARTNERS</div></div>
<nav class="abs nav"><a class="active">HOME</a><a>ABOUT US</a><a>SERVICES</a><a>CONTACT US</a></nav>
<div class="abs hero-phone"><div class="ring"><svg width="16" height="16" viewBox="0 0 24 24"><path d="M6.6 10.8a15 15 0 0 0 6.6 6.6l2.2-2.2a1 1 0 0 1 1-.25 11 11 0 0 0 3.6.6 1 1 0 0 1 1 1V20a1 1 0 0 1-1 1A17 17 0 0 1 3 4a1 1 0 0 1 1-1h3.5a1 1 0 0 1 1 1 11 11 0 0 0 .6 3.6 1 1 0 0 1-.25 1z" fill="#fff"/></svg></div>01 555 0142</div>
<h1 class="abs hero-title">Meridale<br>Partners</h1>
<div class="abs hero-sub">Data Analytics &amp;<br>Epm Consulting Services</div>
<svg class="abs" style="left:74px;top:652px" width="100" height="40" viewBox="0 0 100 40"><path d="M18 3 2 20l16 17" stroke="#fff" stroke-width="3" fill="none"/><path d="M66 3l16 17-16 17" stroke="#ff7a00" stroke-width="3" fill="none"/></svg>
<div class="abs scroll">Scroll down</div>
<div class="abs scroll-line"></div>

<div class="abs label" style="left:75px;top:842px">ABOUT US</div>
<h2 class="abs h2" style="left:74px;top:867px">Who We Are</h2>
<p class="abs about-lead">MP are a Data Analytics &amp; EPM company, specialising in the<br>implementation and support of Business Intelligence, EPM<br>and Data Analytics business solutions, both in the<br>Cloud and on-premise.</p>
<p class="abs about-body">Meridale Partners is an exciting start-up in the Data Analytics<br>and EPM space.&nbsp; Founded in 2019, MP specialise in the<br>implementation and support of BI, EPM and Data Analytics business<br>solutions, both in the Cloud and on-premise.</p>
<div class="abs btn" style="left:74px;top:1206px;width:160px;height:46px">Learn More</div>
<div class="abs photo" style="left:616px;top:841px;width:248px;height:216px" role="img" aria-label="Photo of an analyst looking at a dashboard on a monitor"></div>
<div class="abs photo" style="left:616px;top:1070px;width:248px;height:216px" role="img" aria-label="Photo of a hand on a desk in front of a monitor"></div>
<div class="abs photo warm" style="left:878px;top:900px;width:248px;height:327px" role="img" aria-label="Photo of a woman pointing at a chart on a screen"></div>

<div class="abs services" role="img" aria-label="Dark blue background photo of office towers"></div>
<div class="abs label" style="left:0;width:1200px;text-align:center;top:1433px">OUR SERVICES</div>
<h2 class="abs h2" style="left:0;width:1200px;text-align:center;top:1458px;color:#fff">What We Do</h2>

<div class="abs svc" style="left:74px;top:1537px">
  <div class="dome" style="top:-118px"></div>
  <svg class="abs" style="left:132px;top:8px" width="66" height="68" viewBox="0 0 66 68" fill="none" stroke="#fff" stroke-width="2.5"><circle cx="22" cy="28" r="9"/><path d="M4 66V54a10 10 0 0 1 10-10h16a10 10 0 0 1 10 10v12"/><rect x="36" y="4" width="28" height="20" rx="3"/><path d="M42 11h16M42 17h10"/></svg>
  <h3 style="top:118px">Advise &amp; Architect</h3>
  <p style="top:152px">Helping our customers understand the art of the possible and safeguarding their investments by overseeing implementations.</p>
</div>
<div class="abs svc" style="left:436px;top:1537px">
  <h3 style="top:26px">Design &amp; Implement</h3>
  <p style="top:60px">Helping our customers understand the art of the possible and safeguarding their investments by overseeing implementations.</p>
  <div class="dome" style="top:180px"></div>
  <svg class="abs" style="left:132px;top:190px" width="66" height="66" viewBox="0 0 66 66" fill="none" stroke="#fff" stroke-width="2.5"><circle cx="22" cy="16" r="9"/><path d="M4 64V48a10 10 0 0 1 10-10h14"/><path d="M40 6v16h22V6"/><circle cx="50" cy="50" r="7"/><circle cx="50" cy="50" r="13" stroke-dasharray="5 4"/></svg>
</div>
<div class="abs svc" style="left:797px;top:1537px">
  <div class="dome" style="top:-118px"></div>
  <svg class="abs" style="left:130px;top:8px" width="70" height="68" viewBox="0 0 70 68" fill="none" stroke="#fff" stroke-width="2.5"><circle cx="18" cy="18" r="12" stroke-dasharray="6 4"/><path d="M34 58V50a16 16 0 1 1 12 0v8z"/><circle cx="56" cy="52" r="10" stroke-dasharray="5 4"/></svg>
  <h3 style="top:118px">Optimise &amp; Manage</h3>
  <p style="top:152px">Helping our customers understand the art of the possible and safeguarding their investments by overseeing implementations.</p>
</div>

<div class="abs label" style="left:75px;top:1950px">WORK PROCESS</div>
<h2 class="abs h2" style="left:74px;top:1973px">How We Do It</h2>
<p class="abs process-body">Sed ut perspiciatis unde omnis iste natus error<br>sit voluptatem accusantium doloremque<br>laudantium, totam rem aperiam, eaque ipsa<br>quae ab illo inventore veritatis et quasi<br>architecto beatae vitae dicta.</p>
<div class="abs btn" style="left:74px;top:2197px;width:160px;height:46px">Learn More</div>

<div class="abs panel"></div>
<div class="abs panel-inner"></div>
<div class="abs step-card"></div>

<div class="abs step dark" style="left:473px;top:1993px">
  <svg width="70" height="58" viewBox="0 0 70 58" fill="none" stroke="#ff7a00" stroke-width="2.5"><rect x="16" y="2" width="22" height="16" rx="2"/><rect x="34" y="10" width="20" height="14" rx="2"/><circle cx="16" cy="34" r="6"/><circle cx="54" cy="34" r="6"/><path d="M4 56v-6a8 8 0 0 1 8-8h8a8 8 0 0 1 8 8v6M42 56v-6a8 8 0 0 1 8-8h8a8 8 0 0 1 8 8v6"/></svg>
  <h4>Heading 1</h4>
  <p>Sed ut perspiciatis unde omnis iste natus error sit voluptatem accusa</p>
  <svg style="margin-top:12px" width="30" height="20" viewBox="0 0 30 20"><circle cx="9" cy="10" r="8" fill="#fff"/><path d="M12 10h14M20 4l6 6-6 6" stroke="#ff7a00" stroke-width="2.5" fill="none"/></svg>
</div>
<div class="abs step light" style="left:683px;top:1995px">
  <svg width="64" height="62" viewBox="0 0 64 62" fill="none" stroke="#ff7a00" stroke-width="2.5"><circle cx="32" cy="31" r="22" stroke-dasharray="9 5"/><path d="M26 42v-4a10 10 0 1 1 12 0v4z"/></svg>
  <h4>Heading 2</h4>
  <p>Sed ut perspiciatis unde omnis iste natus error sit voluptatem accusa</p>
  <svg style="margin-top:12px" width="30" height="20" viewBox="0 0 30 20"><circle cx="9" cy="10" r="8" fill="#fde4cc"/><path d="M12 10h14M20 4l6 6-6 6" stroke="#ff7a00" stroke-width="2.5" fill="none"/></svg>
</div>
<div class="abs step dark" style="left:892px;top:1993px">
  <svg width="64" height="58" viewBox="0 0 64 58" fill="none" stroke="#ff7a00" stroke-width="2.5"><circle cx="44" cy="16" r="11" stroke-dasharray="6 4"/><path d="M14 52v-6a14 14 0 1 1 14 0v6z"/><path d="M6 10l4 4M36 36l6 4M2 26h6"/></svg>
  <h4>Heading 3</h4>
  <p>Sed ut perspiciatis unde omnis iste natus error sit voluptatem accusa</p>
  <svg style="margin-top:12px" width="30" height="20" viewBox="0 0 30 20"><circle cx="9" cy="10" r="8" fill="#fff"/><path d="M12 10h14M20 4l6 6-6 6" stroke="#ff7a00" stroke-width="2.5" fill="none"/></svg>
</div>

<div class="abs cta"></div>
<div class="abs cta-text">CONTACT US TO DISCUSS YOUR BUSINESS NEEDS</div>
<div class="abs btn" style="left:773px;top:2380px;width:160px;height:45px;font-size:18px;gap:6px"><svg width="14" height="14" viewBox="0 0 24 24"><path d="M6.6 10.8a15 15 0 0 0 6.6 6.6l2.2-2.2a1 1 0 0 1 1-.25 11 11 0 0 0 3.6.6 1 1 0 0 1 1 1V20a1 1 0 0 1-1 1A17 17 0 0 1 3 4a1 1 0 0 1 1-1h3.5a1 1 0 0 1 1 1 11 11 0 0 0 .6 3.6 1 1 0 0 1-.25 1z" fill="#fff"/></svg>01 555 0142</div>
<div class="abs btn" style="left:941px;top:2380px;width:160px;height:45px;font-size:18px;gap:6px"><svg width="18" height="14" viewBox="0 0 18 14"><rect width="18" height="14" rx="1.5" fill="#fff"/><path d="M1 1l8 6 8-6" stroke="#ff7a00" stroke-width="1.6" fill="none"/></svg>Contact Us</div>

<footer class="abs footer"></footer>
<div class="abs brand" style="left:74px;top:2540px;font-size:17px;line-height:20px"><div class="brand-mark" style="width:52px;height:52px;border-width:6px"></div><div>MERIDALE<br>PARTNERS</div></div>
<p class="abs f-copy">Copyright © 2022.&nbsp; Meridale Partners<br>All Rights Reserved.</p>

<div class="abs f-head" style="left:370px;top:2510px">SITE MAP</div>
<div class="abs f-list" style="left:370px;top:2538px">Home<br>Services<br>About Us<br>Contact Us</div>

<div class="abs f-head" style="left:560px;top:2510px">CONTACT US</div>
<div class="abs f-contact" style="top:2545px"><svg width="16" height="14" viewBox="0 0 16 14" style="margin-top:4px"><path d="M0 2l5-2 6 2 5-2v12l-5 2-6-2-5 2z" fill="#ff7a00"/></svg><span>14 Harbour View Road,<br>Eastfield, Kilbarra 4,<br>K04 RT27</span></div>
<div class="abs f-contact" style="top:2629px"><svg width="14" height="14" viewBox="0 0 24 24" style="margin-top:4px"><path d="M6.6 10.8a15 15 0 0 0 6.6 6.6l2.2-2.2a1 1 0 0 1 1-.25 11 11 0 0 0 3.6.6 1 1 0 0 1 1 1V20a1 1 0 0 1-1 1A17 17 0 0 1 3 4a1 1 0 0 1 1-1h3.5a1 1 0 0 1 1 1 11 11 0 0 0 .6 3.6 1 1 0 0 1-.25 1z" fill="#ff7a00"/></svg><span>01 555 0142</span></div>
<div class="abs f-contact" style="top:2665px"><svg width="14" height="12" viewBox="0 0 18 14" style="margin-top:5px"><rect x="1" y="1" width="16" height="12" fill="none" stroke="#ff7a00" stroke-width="2"/><path d="M1 1l8 6 8-6" stroke="#ff7a00" stroke-width="2" fill="none"/></svg><span>info@meridale-partners.example</span></div>

<div class="abs f-head" style="left:885px;top:2510px">PARTNER</div>
<div class="abs partner-badge" role="img" aria-label="Technology partner badge"></div>
<div class="abs f-head" style="left:885px;top:2610px">FOLLOW US</div>
<div class="abs social" role="list" aria-label="Social channels">
  <i role="listitem" aria-label="Social channel 1"></i>
  <i role="listitem" aria-label="Social channel 2"></i>
  <i role="listitem" aria-label="Social channel 3"></i>
  <i role="listitem" aria-label="Social channel 4"></i>
  <i role="listitem" aria-label="Social channel 5"></i>
</div>

</body>
</html>
```